Email Signature Block Design for Law Firm

I would like you to create a similar signature block for my law firm . I saw the email signature block attached as image002.png and wanted a similar design for my law firm. I want to be able to swap the portraits for each of my staff from the final design. Our law firm colors are black, gold, white, red.

Industry/Entity Type

Law

Requirements
Nice to have
• i like the red circle in around the photo in the tall oak group design. The Silver Lark Co desgn is what inspired me to have a signature block design for my firm.

```html
<!DOCTYPE html>
<html lang="en">
<head>
<meta charset="UTF-8">
<title>Email Signature – Marcus D. Hale</title>
<link href="https://fonts.googleapis.com/css2?family=Cinzel:wght@500;700&family=Poppins:wght@300;400;600&display=swap" rel="stylesheet">
<style>
  :root{
    --gold:#dc9c2c;
    --red:#d10f0f;
    --ink:#141414;
    --dark:#0b0b0b;
    --white:#ffffff;
    --stage:#726e6d;
  }
  *{margin:0;padding:0;box-sizing:border-box}
  html,body{width:1200px;height:600px;overflow:hidden;background:var(--stage)}
  .signature{
    position:absolute;left:75px;top:169px;width:1050px;height:247px;
    background:linear-gradient(90deg,#e9e9e9 0%,#fafafa 40%,#ffffff 70%,#f3f3f3 100%);
    box-shadow:0 0 40px rgba(0,0,0,.45);
    overflow:hidden;
    font-family:'Poppins',sans-serif;color:var(--ink);
  }
  .signature__art{position:absolute;left:0;top:0;width:1050px;height:247px}
  .name{
    position:absolute;left:345px;top:30px;
    font-family:'Cinzel',serif;font-weight:700;font-size:40px;line-height:1;
    color:var(--red);white-space:nowrap;
  }
  .role{
    position:absolute;left:344px;top:76px;
    font-size:21px;font-weight:400;line-height:1;white-space:nowrap;
  }
  .rule{position:absolute;left:345px;top:105px;width:383px;height:1.5px;background:var(--red)}
  .contact{position:absolute;display:flex;align-items:center;gap:8px;font-size:13.5px;white-space:nowrap;line-height:1}
  .contact svg{width:11px;height:11px;flex:none}
  .contact--phone{left:343px;top:119px}
  .contact--email{left:490px;top:119px}
  .contact--address{left:343px;top:146px}
  .contact--web{left:343px;top:170px;letter-spacing:4.2px;font-size:13.5px}
  .follow{position:absolute;left:343px;top:196px;display:flex;align-items:center;white-space:nowrap}
  .follow__label{font-weight:600;font-size:13px;letter-spacing:1.6px;color:var(--red);margin-right:14px}
  .follow__dot{width:13px;height:13px;border-radius:50%;background:var(--gold);margin-right:23px}
  .firm{position:absolute;left:806px;top:70px;width:200px;text-align:center;color:var(--ink)}
  .firm__mark{width:80px;height:80px;background:var(--gold);margin:0 auto 38px}
  .firm__name{font-family:'Cinzel',serif;font-weight:500;font-size:14.5px;line-height:1;white-space:nowrap}
  .firm__tag{
    display:flex;align-items:center;gap:5px;margin-top:3px;
    font-family:'Cinzel',serif;font-weight:500;font-size:6.5px;letter-spacing:3px;white-space:nowrap;
  }
  .firm__tag::before,.firm__tag::after{content:"";flex:1;height:1px;background:var(--ink)}
</style>
</head>
<body>
<div class="signature">
  <svg class="signature__art" viewBox="125 281 1751 411" preserveAspectRatio="none" aria-hidden="false">
    <defs>
      <linearGradient id="darkFade" x1="0" x2="1">
        <stop offset="0" stop-color="#050505"/>
        <stop offset=".55" stop-color="#1a1a1a"/>
        <stop offset="1" stop-color="#1a1a1a" stop-opacity="0"/>
      </linearGradient>
      <linearGradient id="portraitTone" x1="0" y1="0" x2="0" y2="1">
        <stop offset="0" stop-color="#f2f2f2"/>
        <stop offset=".45" stop-color="#8a6a58"/>
        <stop offset="1" stop-color="#1b1c22"/>
      </linearGradient>
    </defs>
    <rect class="backdrop-dark" x="125" y="281" width="480" height="411" fill="url(#darkFade)" role="img" aria-label="Dark courtroom backdrop"/>
    <polygon class="accent-gold" points="222,490 345,281 565,281 520,340 310,340 245,490" fill="var(--gold)"/>
    <polygon class="accent-red-base" points="275,692 340,625 545,625 500,692" fill="var(--red)"/>
    <polygon class="accent-red-frame" points="505,330 527,330 617,493 532,650 510,650 598,493" fill="var(--red)"/>
    <polygon class="portrait-frame" points="245,490 330,332 510,332 600,493 520,645 340,645" fill="var(--white)"/>
    <polygon class="portrait" points="262,490 340,345 500,345 582,493 510,640 350,640" fill="url(#portraitTone)" role="img" aria-label="Staff portrait photo"/>
  </svg>

  <h1 class="name">Marcus D. Hale</h1>
  <p class="role">PERSONAL INJURY LAWYER</p>
  <div class="rule"></div>

  <p class="contact contact--phone">
    <svg viewBox="0 0 12 12"><circle cx="6" cy="6" r="6" fill="var(--gold)"/><path d="M4 3.2l1 1.3-.6.7a4 4 0 0 0 2.4 2.4l.7-.6 1.3 1-.6 1C6 8.8 3.2 6 3 4z" fill="#fff"/></svg>
    555-014-2290
  </p>
  <p class="contact contact--email">
    <svg viewBox="0 0 12 12"><circle cx="6" cy="6" r="6" fill="var(--gold)"/><rect x="3" y="4" width="6" height="4" fill="none" stroke="#fff" stroke-width=".8"/><path d="M3 4l3 2.3L9 4" fill="none" stroke="#fff" stroke-width=".8"/></svg>
    hale@halelawgroup.com
  </p>
  <p class="contact contact--address">
    <svg viewBox="0 0 12 12"><path d="M6 .5a4 4 0 0 1 4 4c0 3-4 7-4 7s-4-4-4-7a4 4 0 0 1 4-4z" fill="var(--gold)"/><circle cx="6" cy="4.5" r="1.5" fill="#fff"/></svg>
    120 Harbor Ave., Suite 300, Bayview, FL 32000
  </p>
  <p class="contact contact--web">
    <svg viewBox="0 0 12 12"><circle cx="6" cy="6" r="6" fill="var(--gold)"/><circle cx="6" cy="6" r="3.5" fill="none" stroke="#fff" stroke-width=".7"/><path d="M2.5 6h7M6 2.5c-1.5 2-1.5 5 0 7M6 2.5c1.5 2 1.5 5 0 7" fill="none" stroke="#fff" stroke-width=".6"/></svg>
    www.halelawgroup.com
  </p>

  <div class="follow">
    <span class="follow__label">FOLLOW US ON</span>
    <span class="follow__dot"></span>
    <span class="follow__dot"></span>
    <span class="follow__dot"></span>
    <span class="follow__dot"></span>
    <span class="follow__dot"></span>
  </div>

  <div class="firm">
    <div class="firm__mark"></div>
    <p class="firm__name">THE HALE FIRM, PLLC</p>
    <p class="firm__tag">Attorneys At Law</p>
  </div>
</div>
</body>
</html>
```